TA BRAMLEY BUSINESS CARD DESIGN PROJECT

We need to utilize our logo that was expertly created on PixelHarbor and now need to match this with a business card design.

```html
<!DOCTYPE html>
<html lang="en">
<head>
<meta charset="UTF-8">
<title>TA Bramley Business Card</title>
<link href="https://fonts.googleapis.com/css2?family=Lato:wght@400;700;900&display=swap" rel="stylesheet">
<style>
  :root {
    --brand-blue: #0455ad;
    --card-white: #ffffff;
    --backdrop: #232323;
    --ink-light: #ffffff;
  }
  * { margin: 0; padding: 0; box-sizing: border-box; }
  html, body { width: 1200px; height: 875px; overflow: hidden; }
  body {
    background: var(--backdrop);
    font-family: "Lato", sans-serif;
    position: relative;
  }
  .card {
    position: absolute;
    width: 540px;
    height: 309px;
    border-radius: 18px;
    overflow: hidden;
    top: 283px;
  }
  .card--front { left: 40px; background: var(--brand-blue); }
  .card--back { left: 620px; background: var(--card-white); }

  .wordmark {
    position: absolute;
    font-family: "Lato", sans-serif;
    font-weight: 900;
    letter-spacing: 0.12em;
    white-space: nowrap;
    display: flex;
    align-items: center;
    gap: 14px;
  }
  .wordmark__dot {
    width: 22px; height: 22px; border-radius: 50%;
  }
  .card--front .wordmark {
    left: 50%; top: 50%; transform: translate(-50%, -50%);
    color: var(--ink-light); font-size: 44px;
  }
  .card--front .wordmark__dot { background: var(--ink-light); }

  .back-shapes { position: absolute; inset: 0; }
  .card--back .wordmark {
    left: 390px; top: 118px; transform: translateX(-50%);
    color: var(--brand-blue); font-size: 27px; gap: 10px;
  }
  .card--back .wordmark__dot { background: var(--brand-blue); width: 16px; height: 16px; }

  .contact {
    position: absolute;
    left: 34px; top: 66px;
    color: var(--ink-light);
  }
  .contact__name { font-weight: 900; font-size: 22px; letter-spacing: 0.02em; }
  .contact__role { font-size: 15px; margin-top: 2px; }
  .contact__address { font-size: 13px; margin-top: 14px; line-height: 1.4; }
  .contact__list { list-style: none; margin-top: 12px; font-size: 13px; line-height: 1.55; }
  .contact__list li { display: flex; align-items: center; gap: 9px; }
  .contact__list svg { width: 11px; height: 11px; fill: var(--ink-light); flex: none; }
</style>
</head>
<body>

<section class="card card--front" aria-label="Business card front">
  <div class="wordmark"><span class="wordmark__dot"></span>TA BRAMLEY</div>
</section>

<section class="card card--back" aria-label="Business card back">
  <svg class="back-shapes" viewBox="0 0 540 309" preserveAspectRatio="none" aria-hidden="true">
    <rect x="0" y="0" width="298" height="309" fill="var(--brand-blue)"/>
    <polygon points="508,180 540,150 540,309 524,309" fill="var(--brand-blue)"/>
  </svg>

  <div class="contact">
    <div class="contact__name">DANIEL HART</div>
    <div class="contact__role">Founder &amp; CEO</div>
    <div class="contact__address">48 Larkfield Rd.<br>Westbrook, NV 80214</div>
    <ul class="contact__list">
      <li><svg viewBox="0 0 12 12"><path d="M2 1l2 0 1 3-1.3 1a7 7 0 0 0 3.3 3.3L8 7l3 1v2c0 .6-.5 1-1 1A9 9 0 0 1 1 2c0-.5.4-1 1-1z"/></svg>(415) 802-3316</li>
      <li><svg viewBox="0 0 12 12"><path d="M3 0h6v12H3zM4 1.5v8h4v-8z"/></svg>(415) 802-3317</li>
      <li><svg viewBox="0 0 12 12"><path d="M3 0h6v3H3zM1 4h10v5H9v3H3V9H1zM4 8v3h4V8z"/></svg>(415) 802-3318</li>
      <li><svg viewBox="0 0 12 12"><path d="M0 2h12v8H0zM1 3l5 4 5-4v-.2H1z"/></svg>hello@tabramley.co</li>
      <li><svg viewBox="0 0 12 12"><path d="M6 0a6 6 0 1 1 0 12A6 6 0 0 1 6 0zm0 1.3a4.7 4.7 0 1 0 0 9.4 4.7 4.7 0 0 0 0-9.4zM5.4 1.3v9.4h1.2V1.3zM1.3 5.4h9.4v1.2H1.3z"/></svg>www.tabramley.co</li>
    </ul>
  </div>

  <div class="wordmark"><span class="wordmark__dot"></span>TA BRAMLEY</div>
</section>

</body>
</html>
```